Ferncrest Roam Wording For Logo & Business card

I have the logo, I just need the "Ferncrest Roam" wording to go with it, and a business card design. The only thing on the business card is the website info. We provide nature connection experiences, and bolster these efforts through writing and host a platform for community around it.

I also have an idea of what it could look like (sketch), though I'm really not sure how it would come out. I am open to the best design and happy to consider original artwork. You can see what the site is about at FerncrestRoam.example.

Contact Information for Business Card

The only thing on the business card is the website info and the design. I will put other messaging on the back.

Website lettering (FerncrestRoam.example) in Montserrat

Logo Text

Ferncrest Roam (letters optional)

Font styles to use
Other font styles liked:
• montserrat

```html
<!DOCTYPE html>
<html lang="en">
<head>
<meta charset="utf-8">
<title>Ferncrest Roam — Business Card</title>
<link rel="stylesheet" href="https://fonts.googleapis.com/css2?family=Montserrat:wght@500;600;800&display=swap">
<style>
  :root {
    --backdrop: #e6e6e4;
    --card-white: #f7f7f6;
    --ink: #1d1430;
    --accent-red: #d0361a;
    --accent-orange: #e86a12;
    --accent-gold: #f2b51a;
    --purple-deep: #130822;
    --purple-mid: #3a1c5a;
    --purple-glow: #8a5aa8;
    --rule: #2a2a2a;
  }
  * { margin: 0; padding: 0; box-sizing: border-box; }
  html, body { width: 1200px; height: 801px; overflow: hidden; }
  body {
    background: var(--backdrop);
    display: flex;
    align-items: center;
    justify-content: center;
    gap: 48px;
    font-family: "Montserrat", Arial, sans-serif;
  }
  .card {
    position: relative;
    width: 520px;
    height: 297px;
    overflow: hidden;
    box-shadow: 0 10px 24px rgba(0,0,0,.18);
  }
  .card--front { background: var(--card-white); }
  .card__swoosh { position: absolute; inset: 0; width: 100%; height: 100%; }

  .brand {
    position: absolute;
    display: flex;
    flex-direction: column;
    align-items: center;
    gap: 14px;
  }
  .brand__dot {
    width: 92px; height: 92px;
    border-radius: 50%;
    background: var(--purple-mid);
  }
  .brand__name {
    font-weight: 800;
    font-size: 25px;
    letter-spacing: .5px;
    white-space: nowrap;
  }
  .card--front .brand { left: 28px; top: 40px; width: 210px; }
  .card--front .brand__name { color: var(--ink); }

  .card__divider {
    position: absolute;
    left: 258px; top: 48px;
    width: 1px; height: 130px;
    background: var(--rule);
  }
  .contact {
    position: absolute;
    left: 276px; top: 86px;
    color: var(--ink);
  }
  .contact__line {
    display: flex;
    align-items: center;
    gap: 8px;
    font-size: 15px;
    font-weight: 600;
    white-space: nowrap;
  }
  .contact__icon { width: 13px; height: 13px; flex: none; }

  .card--back {
    background: radial-gradient(ellipse 55% 75% at 42% 55%, var(--purple-glow) 0%, var(--purple-mid) 45%, var(--purple-deep) 100%);
  }
  .card--back .brand { left: 0; right: 0; top: 52px; }
  .card--back .brand__dot { width: 110px; height: 110px; background: var(--purple-deep); border: 3px solid #fff; }
  .card--back .brand__name { color: #fff; font-size: 32px; }
</style>
</head>
<body>
  <article class="card card--front" aria-label="Business card front">
    <svg class="card__swoosh" viewBox="0 0 520 297" preserveAspectRatio="none" aria-hidden="true">
      <path d="M0 297 L0 274 C130 262 270 214 390 150 C440 124 485 104 520 94 L520 297 Z" fill="var(--accent-gold)"/>
      <path d="M0 297 L0 280 C140 268 280 220 400 156 C448 130 490 112 520 104 L520 297 Z" fill="var(--accent-orange)"/>
      <path d="M0 297 L0 287 C150 275 290 228 410 164 C455 138 492 122 520 114 L520 297 Z" fill="#fff"/>
      <path d="M0 297 C160 284 300 236 420 172 C460 148 495 132 520 126 L520 297 Z" fill="var(--purple-mid)"/>
    </svg>
    <div class="brand">
      <div class="brand__dot"></div>
      <div class="brand__name">Ferncrest Roam</div>
    </div>
    <div class="card__divider"></div>
    <div class="contact">
      <div class="contact__line">
        <svg class="contact__icon" viewBox="0 0 12 12"><circle cx="6" cy="6" r="5.5" fill="var(--accent-red)"/><circle cx="6" cy="6" r="2.2" fill="#fff"/></svg>
        <span>FerncrestRoam.example</span>
      </div>
    </div>
  </article>

  <article class="card card--back" aria-label="Business card back">
    <div class="brand">
      <div class="brand__dot"></div>
      <div class="brand__name">Ferncrest Roam</div>
    </div>
  </article>
</body>
</html>
```